Flat bootstrap design for existing site

I'm looking for a modern flat design based around an existing logo. This has to be a custom design (no external templates), and implemented into a bootstrap framework.

The logo is attached as 2 versions - choose whichever you want, that flows better with whatever design you choose.

Added screenshots of the existing site (currently using the default bootstrap layouts). Please make your designs around those pages in the screenshots (i.e. the homepage only has the postal code input and the header). The active page has 3 screenshots, because I wanted to illustrate the other states that would be visible (in the table rows).

This is a moving/junk removal website, just for some context.

Here's some example websites (flat designs) that I like, just to give you an idea of what I'm after.

https://www.plimvora.com/
https://dacklow.com/
https://trevanu.com/
https://quobrintal.com/en/

Coding

Coded - Design and coding required

Number of Pages Required

5+ page

Colors

Designer to choose colors to be used in the design.

Requirements
Must have
• It must be a modern/simple flat design, that is built around the existing logo (attached).
• It has to be implemented using bootstrap.

```html
<!DOCTYPE html>
<html lang="en">
<head>
<meta charset="utf-8">
<title>Haulora – Sign In</title>
<link href="https://fonts.googleapis.com/css2?family=Raleway:wght@400;500;700;800&display=swap" rel="stylesheet">
<style>
  :root {
    --brand-blue: #4ac9f5;
    --accent-orange: #ff8a00;
    --page-grey: #ebebeb;
    --field-grey: #f2f2f2;
    --white: #ffffff;
    --ink: #262626;
    --nav-ink: #5f5f5f;
    --muted: #555555;
  }
  * { box-sizing: border-box; margin: 0; padding: 0; }
  html, body {
    width: 1200px;
    height: 983px;
    overflow: hidden;
  }
  body {
    background: var(--page-grey);
    font-family: "Raleway", Arial, sans-serif;
    color: var(--ink);
    position: relative;
  }
  .site-header {
    position: absolute;
    top: 0; left: 0;
    width: 1200px;
    height: 104px;
    background: var(--white);
  }
  .brand {
    position: absolute;
    left: 75px;
    top: 30px;
    font-size: 40px;
    font-weight: 800;
    color: var(--brand-blue);
    letter-spacing: 0.5px;
    line-height: 44px;
    text-decoration: none;
  }
  .main-nav {
    position: absolute;
    top: 0;
    right: 72px;
    height: 104px;
    display: flex;
    list-style: none;
  }
  .main-nav a {
    display: block;
    height: 104px;
    line-height: 104px;
    padding: 0 17px;
    font-size: 13.5px;
    font-weight: 700;
    color: var(--nav-ink);
    text-decoration: none;
    text-transform: uppercase;
  }
  .main-nav .is-highlight a {
    background: var(--brand-blue);
    color: var(--white);
    padding: 0 16px;
  }
  .main-nav li:last-child a { padding-right: 0; }
  .signin-card {
    position: absolute;
    left: 75px;
    top: 147px;
    width: 1051px;
    height: 287px;
    background: var(--white);
    border-radius: 3px;
    text-align: center;
  }
  .signin-title {
    font-size: 38px;
    font-weight: 700;
    margin-top: 28px;
    line-height: 46px;
    color: var(--ink);
  }
  .signin-form {
    width: 484px;
    margin: 20px auto 0;
  }
  .field {
    display: block;
    width: 484px;
    height: 46px;
    margin-bottom: 5px;
    border: none;
    border-radius: 2px;
    background: var(--field-grey);
    font-family: "Raleway", Arial, sans-serif;
    font-size: 13.5px;
    font-weight: 500;
    color: var(--ink);
    text-align: center;
  }
  .field::placeholder { color: #333333; }
  .btn-login {
    display: block;
    width: 484px;
    height: 46px;
    margin-top: 7px;
    border: none;
    border-radius: 2px;
    background: var(--accent-orange);
    color: var(--white);
    font-family: "Raleway", Arial, sans-serif;
    font-size: 13px;
    font-weight: 700;
    text-transform: uppercase;
  }
  .site-footer {
    position: absolute;
    left: 0;
    top: 908px;
    width: 1200px;
    height: 75px;
    background: var(--white);
    text-align: center;
  }
  .copyright {
    font-size: 12px;
    color: var(--muted);
    line-height: 75px;
    letter-spacing: 0.2px;
  }
</style>
</head>
<body>
  <header class="site-header">
    <a class="brand" href="#">Haulora</a>
    <ul class="main-nav">
      <li><a href="#">Book</a></li>
      <li><a href="#">How it works</a></li>
      <li class="is-highlight"><a href="#">Become a driver</a></li>
      <li><a href="#">Sign in</a></li>
    </ul>
  </header>

  <main class="signin-card">
    <h1 class="signin-title">Please Sign In</h1>
    <form class="signin-form">
      <input class="field" type="email" placeholder="Email Address">
      <input class="field" type="password" placeholder="Password">
      <button class="btn-login" type="button">Log in</button>
    </form>
  </main>

  <footer class="site-footer">
    <p class="copyright">Copyright © 2017. Company Name. All Right Reserved</p>
  </footer>
</body>
</html>
```